Law Offices business card

Hi there, I'll need business card for the Law Offices of Colin Matheny. The information must convey his strategic approach and quick resolution to complex business litigation needs. Please emphasize Civil Litigation, Corporate Law, Business Governance and Real Estate Law. Colin has over 25 years of experience in these fields.The card should be modern and edgy and the message should be clear. Please consult his current website for ideas.

```html
<!DOCTYPE html>
<html lang="en">
<head>
<meta charset="utf-8">
<title>Law Offices of Colin Matheny – Business Card</title>
<link href="https://fonts.googleapis.com/css2?family=Arimo:wght@400;700&display=swap" rel="stylesheet">
<style>
  :root {
    --backdrop: #3a3b3d;
    --card-black: #050505;
    --accent-red: #c4504f;
    --text-white: #f4f4f4;
    --text-soft: #d8d8d8;
    --text-muted: #a9a9a9;
  }
  * { margin: 0; padding: 0; box-sizing: border-box; }
  html, body {
    width: 1200px; height: 950px; overflow: hidden;
    background: var(--backdrop);
    font-family: "Arimo", Arial, sans-serif;
  }
  .card {
    position: absolute;
    width: 700px; height: 400px;
    background: var(--card-black);
    color: var(--text-white);
    overflow: hidden;
  }
  /* back side */
  .card-back { left: 110px; top: 55px; }
  .back-mark {
    position: absolute; left: 0; right: 0; top: 118px;
    display: flex; justify-content: center; align-items: center; gap: 12px;
    font-size: 24px; font-weight: 700; letter-spacing: 1px;
  }
  .back-mark .mark-square { width: 16px; height: 16px; background: var(--accent-red); }
  .practice-areas {
    position: absolute; left: 40px; right: 40px; top: 172px;
    display: flex; justify-content: center; align-items: center; gap: 10px;
    list-style: none;
    font-size: 12px; letter-spacing: 1px; text-transform: uppercase; color: var(--text-soft);
  }
  .practice-areas li { display: flex; align-items: center; gap: 10px; white-space: nowrap; }
  .practice-areas li + li::before {
    content: ""; width: 5px; height: 5px; background: var(--accent-red);
  }
  .experience {
    position: absolute; left: 0; right: 0; top: 200px;
    text-align: center; font-size: 13px; letter-spacing: 1px; color: var(--text-muted);
  }
  .back-web {
    position: absolute; left: 0; right: 0; top: 262px;
    display: flex; justify-content: center; align-items: center; gap: 14px;
    font-size: 15px; letter-spacing: 4px; color: var(--text-soft);
  }
  .back-web .rule { width: 60px; height: 2px; background: var(--accent-red); }

  /* front side */
  .card-front { left: 390px; top: 495px; }
  .title-band {
    position: absolute; left: 0; top: 0; width: 100%; height: 92px;
    background: var(--accent-red);
    text-align: right; padding: 22px 32px 0 0;
  }
  .person-name { font-size: 22px; font-weight: 700; }
  .person-role { font-size: 16px; margin-top: 4px; }
  .firm-name {
    position: absolute; left: 36px; top: 168px;
    display: flex; align-items: center; gap: 10px;
    font-size: 19px; font-weight: 700; line-height: 1.15;
  }
  .firm-name .mark-square { width: 14px; height: 14px; background: var(--accent-red); flex: none; }
  .contact-list {
    position: absolute; left: 86px; top: 260px;
    list-style: none; font-size: 16px; line-height: 25px; color: var(--text-soft);
  }
  .contact-list li { display: flex; align-items: center; gap: 10px; }
  .contact-list svg { width: 14px; height: 14px; fill: var(--accent-red); flex: none; }
  .address {
    position: absolute; right: 32px; top: 170px;
    text-align: right; font-size: 16px; line-height: 24px; color: var(--text-soft);
    font-style: normal;
  }
  .address .web { letter-spacing: 3px; }
</style>
</head>
<body>
  <section class="card card-back">
    <div class="back-mark"><span class="mark-square"></span><span>Colin Matheny</span></div>
    <ul class="practice-areas">
      <li>Civil Litigation</li>
      <li>Corporate Law</li>
      <li>Business Governance</li>
      <li>Real Estate Law</li>
    </ul>
    <p class="experience">Over 25 years of strategic, swift resolution</p>
    <div class="back-web"><span class="rule"></span><span>www.mathenylaw.example</span><span class="rule"></span></div>
  </section>

  <section class="card card-front">
    <header class="title-band">
      <div class="person-name">Evan Marlowe</div>
      <div class="person-role">President</div>
    </header>

    <div class="firm-name"><span class="mark-square"></span><span>Law Offices of<br>Colin Matheny, PA</span></div>

    <ul class="contact-list">
      <li><svg viewBox="0 0 16 16"><path d="M3 1h3l1 4-2 1.5a9 9 0 0 0 4.5 4.5L11 9l4 1v3a2 2 0 0 1-2 2A12 12 0 0 1 1 3a2 2 0 0 1 2-2z"/></svg>555 0142 7781</li>
      <li><svg viewBox="0 0 16 16"><path d="M4 0h8a1 1 0 0 1 1 1v14a1 1 0 0 1-1 1H4a1 1 0 0 1-1-1V1a1 1 0 0 1 1-1zm1 2v10h6V2z"/></svg>555 0198 3364</li>
      <li><svg viewBox="0 0 16 16"><path d="M4 0h8v5H4zM1 6h14v7h-3v3H4v-3H1zm5 5v3h4v-3z"/></svg>555 0173 2219</li>
      <li><svg viewBox="0 0 16 16"><path d="M0 3h16v10H0zm1.5 1.5L8 9l6.5-4.5V4h-13z"/></svg>evan@mathenylaw.example</li>
    </ul>

    <address class="address">
      2190 Harlow Crest Road<br>
      Linden Vale, NY 11920<br>
      <span class="web">www.mathenylaw.example</span>
    </address>
  </section>
</body>
</html>
```